Create a Brochure Design for Brantley Homecare

Brantley Homecare is a subsidiary of the Brantley Care Group. This brochure is specifically for the Brantley Homecare company and brand. Create a 3 panel, A4, front and back, tri-fold brochure. This brochure will be a way to introduce our Homecare services to the community, prospective clients, and various referral partners. The brochure must be eye catching, unique in its deliverables and demonstrate both attention to detail and comfort. Our organization is sophisticated and built around warmth, care and individualized personal attention. The most important aspect of this design is to focus on creating a nurturing, warm, and inviting feel where you would want to have a Nurse or Nurse’s Aide in your own home or a loved one’s home.

I am open to the creativity of the designer to develop something based on the above criteria; however I would like the design to work well with the existing collateral material. What I mean by that is that while I want everything to have its own personality and stand out as its own brand representative, I still need to be able to tell that the overall design concept stays stylistically inside of the same ‘family’ of existing designed material. Because of this, below I would like for the designer to pull inspiration from the link to our website (Located below) as well as from the attachment of our recently refreshed business cards (Attached). This should allow each design to be unique and creative, while still staying inside of a framework and the feel/style that I am looking for.

Finally, I want all the designers to understand that this brochure design is for a private, in home, healthcare company where we are responsible for providing personalized care for a culturally and ethnically diverse make-up clientele of all ages. The photos that are used must represent an image of warmth, care, and a positive interaction between client and caregiver.

Look under the Brantley Homecare tab at www.brantleycaregroup.example

Industry/Entity Type

Healthcare

Requirements
Must have
• • The Brantley Homecare company logo must be included.

```html
<!DOCTYPE html>
<html lang="en">
<head>
<meta charset="utf-8">
<title>Brantley Homecare – Tri-fold Brochure, Inside Spread</title>
<link rel="stylesheet" href="https://fonts.googleapis.com/css2?family=Cormorant+Garamond:wght@700&family=Crimson+Text:ital,wght@0,400;0,600;1,400&display=swap">
<style>
  :root {
    --page-bg: #e6e3e0;
    --paper: #ffffff;
    --teal: #1d7a70;
    --salmon: #ef9e88;
    --salmon-soft: #f7cfc1;
    --ink: #3a3a3a;
    --photo-warm-a: #e9d9c8;
    --photo-warm-b: #d79f8d;
    --photo-room-a: #cdb79f;
    --photo-room-b: #8c9fb0;
    --photo-green-a: #b8d77a;
    --photo-green-b: #f1dcc8;
  }
  * { box-sizing: border-box; margin: 0; padding: 0; }
  html, body { width: 1200px; height: 800px; overflow: hidden; }
  body {
    background: var(--page-bg);
    font-family: "Crimson Text", Georgia, serif;
    color: var(--ink);
  }
  .brochure {
    position: absolute;
    left: 90px; top: 40px;
    width: 1020px; height: 720px;
    display: flex;
    background: var(--paper);
    box-shadow: 0 6px 24px rgba(0,0,0,.18);
  }
  .panel {
    position: relative;
    width: 340px; height: 720px;
    overflow: hidden;
    background: var(--paper);
  }
  .panel + .panel { border-left: 1px solid #ece8e4; }
  .panel-heading {
    font-family: "Cormorant Garamond", "Crimson Text", serif;
    font-weight: 700;
    color: var(--teal);
    font-size: 26px;
    line-height: 1;
    margin-bottom: 12px;
  }
  .panel-text {
    position: absolute;
    left: 30px; right: 28px;
    font-size: 13.5px;
    line-height: 1.32;
  }
  .panel-text p { margin-bottom: 10px; }
  .lead-letter { color: var(--teal); font-size: 24px; font-weight: 600; line-height: 1; }
  .list-title {
    color: var(--teal);
    font-weight: 600;
    font-size: 15px;
    line-height: 1.25;
    margin-bottom: 6px;
  }
  .bullet-list { list-style: none; margin-bottom: 18px; }
  .bullet-list li { padding-left: 14px; position: relative; margin-bottom: 2px; }
  .bullet-list li::before { content: "•"; position: absolute; left: 0; }
  .service-item { padding-left: 14px; position: relative; }
  .service-item::before { content: "•"; position: absolute; left: 0; color: var(--teal); }
  .service-name { color: var(--teal); font-weight: 600; display: block; }
  .photo { position: absolute; left: 0; right: 0; }
  .photo-reading { top: 440px; bottom: 0; background: linear-gradient(135deg, var(--photo-warm-a), var(--photo-warm-b)); }
  .photo-visit { top: 0; height: 240px; background: linear-gradient(160deg, var(--photo-room-a), var(--photo-room-b)); }
  .photo-hands { top: 450px; bottom: 0; background: radial-gradient(circle at 75% 30%, var(--photo-green-a), #8fbf5a 55%, var(--photo-green-b)); }
  .wave { position: absolute; left: 0; width: 340px; }
  .wave .band { fill: var(--salmon); }
  .wave .band-soft { fill: var(--salmon-soft); }
  .wave .paper { fill: var(--paper); }
</style>
</head>
<body>
<main class="brochure">

  <section class="panel panel-about">
    <div class="panel-text" style="top:32px">
      <h2 class="panel-heading">About</h2>
      <p><span class="lead-letter">B</span>rantley Homecare is a state licensed private duty home health agency serving the local community with pride since 1995.</p>
      <p>We provide in-home services ranging from help with bathing and dressing to personal care and skilled nursing support.</p>
      <p>We strive to give compassionate, dependable care of the highest quality while making each client comfortable. Everything we do is planned around meeting the individual needs of our clients.</p>
      <p>Whether you need a little help or a lot of help, you'll find that Brantley Homecare's services are a cut above the rest.</p>
      <p>The Brantley Way is special. It is compassionate, professional, dependable, and flexible.</p>
    </div>
    <div class="photo photo-reading" role="img" aria-label="Photo of a caregiver reading a book with an elderly woman at home"></div>
    <svg class="wave" style="top:410px;height:90px" viewBox="0 0 340 90" preserveAspectRatio="none" aria-hidden="true">
      <path class="paper" d="M0 0 H340 V22 C230 72 110 2 0 32 Z"/>
      <path class="band" d="M0 30 C110 0 230 70 340 20 L340 48 C230 98 110 28 0 58 Z"/>
    </svg>
  </section>

  <section class="panel panel-team">
    <div class="photo photo-visit" role="img" aria-label="Photo of a nurse and a family member sitting with an elderly man on a sofa"></div>
    <svg class="wave" style="top:170px;height:120px" viewBox="0 0 340 120" preserveAspectRatio="none" aria-hidden="true">
      <path class="band-soft" d="M0 8 C100 8 180 70 340 58 L340 72 C180 90 100 30 0 26 Z"/>
      <path class="band" d="M0 26 C100 30 180 90 340 72 L340 92 C180 110 100 48 0 44 Z"/>
      <path class="paper" d="M0 44 C100 48 180 110 340 92 V120 H0 Z"/>
    </svg>
    <div class="panel-text" style="top:318px">
      <p class="list-title">All of our Care Professionals:</p>
      <ul class="bullet-list">
        <li>Are bonded, insured, and supervised</li>
        <li>Have passed both criminal and abuse background checks</li>
        <li>Have been screened for TB</li>
        <li>Are certified in CPR and First Aid</li>
      </ul>
      <p class="list-title">All client care is supervised by a licensed Nurse Care Consultant whose duties include:</p>
      <ul class="bullet-list">
        <li>Regular home visits</li>
        <li>Client evaluation</li>
        <li>Care Professional supervision</li>
        <li>Revising/updating client care plans</li>
        <li>24/7 phone support</li>
      </ul>
    </div>
  </section>

  <section class="panel panel-services">
    <div class="panel-text" style="top:32px">
      <h2 class="panel-heading">Services</h2>
      <p>Brantley Homecare provides two different levels of care. Our Nurse Care Consultant will meet the client and family to determine the appropriate level of care needed during the complimentary initial consultation.</p>
      <p class="service-item"><span class="service-name">Nurse Aide Care</span>Our Nurse Aides help you with your personal care needs, provide companionship, run errands, and do light housekeeping, along with assisting you with the activities of daily living.</p>
      <p class="service-item"><span class="service-name">Skilled Nursing Care</span>We offer a wide range of skilled nursing services using RNs and LPNs who provide treatment from wound care to life support, in addition to all of the services performed by our Nurse Aides.</p>
    </div>
    <div class="photo photo-hands" role="img" aria-label="Photo of a caregiver gently holding an elderly person's hands"></div>
    <svg class="wave" style="top:420px;height:90px" viewBox="0 0 340 90" preserveAspectRatio="none" aria-hidden="true">
      <path class="paper" d="M0 0 H340 V26 C230 66 110 6 0 30 Z"/>
      <path class="band" d="M0 28 C110 4 230 64 340 24 L340 46 C230 90 110 30 0 52 Z"/>
    </svg>
  </section>

</main>
</body>
</html>
```